Dynamic Business Card for Sports Supplements Company

Hi! I'm looking for an awesome business card to match my existing sports supplement company. I have uploaded my current company logo and screenshot of the front page of my website.

I would like to have something dynamic and interesting and utilize the colors in the website - the reds and purples

The business card should be double sided and focus on a unique eye-catching design on the back and include all the relevant company info.

Most importantly, it should say somewhere: "Sign up on our website for a coupon code."

Target Market(s)

Mostly for women gym goers but it shouldn't be too feminine. It should be in keeping with the website design. It should flow and clearly be connected to it

Industry/Entity Type

Business

Contact Information for Business Card

Lorraine K. Vestal
CEO
LVestal@Quorvanexco.com
www.quorvanexco.com
555.417.3820
P.O. Box 47315
Alder Bay, Oregon 00000

Sign up on our website for a coupon code

Font styles to use
Serif
Sans Serif
Other font styles liked:
• Novecento font family and "Quorvanex" is in AR Destine font

Requirements
Must have
• One side should be a bold Quorvanex logo design. Even just the symbol itself may be o.k. (see attached file)

```html
<!DOCTYPE html>
<html lang="en">
<head>
<meta charset="utf-8">
<title>Quorvanex Business Card</title>
<link rel="stylesheet" href="https://fonts.googleapis.com/css2?family=Arimo:wght@400&display=swap">
<style>
  :root {
    --backdrop: #e6e3df;
    --card: #161617;
    --card-edge: #232325;
    --red: #d8232a;
    --white: #f4f4f4;
    --grey: #8d8d8f;
    --rule: #bdbdbd;
  }
  * { margin: 0; padding: 0; box-sizing: border-box; }
  html, body {
    width: 1200px;
    height: 864px;
    overflow: hidden;
    background: var(--backdrop);
    font-family: "Arimo", Arial, sans-serif;
  }
  .sheet {
    position: relative;
    width: 1200px;
    height: 864px;
  }
  .card {
    position: absolute;
    top: 277px;
    width: 540px;
    height: 309px;
    background: var(--card);
    border: 1px solid var(--card-edge);
    border-radius: 3px;
    box-shadow: 0 10px 28px rgba(0,0,0,0.25);
    overflow: hidden;
  }
  .card--back { left: 40px; }
  .card--front { left: 620px; }

  /* Back side */
  .brand-mark {
    position: absolute;
    left: 70px;
    top: 95px;
    display: flex;
    align-items: center;
    gap: 14px;
  }
  .brand-mark__square {
    width: 34px;
    height: 34px;
    background: var(--red);
  }
  .brand-mark__name {
    font-size: 46px;
    letter-spacing: 3px;
    text-transform: uppercase;
    color: var(--white);
    line-height: 1;
  }
  .coupon-note {
    position: absolute;
    left: 48px;
    top: 196px;
    font-size: 12.5px;
    color: var(--grey);
    letter-spacing: 0.2px;
  }

  /* Front side */
  .contact {
    position: absolute;
    left: 24px;
    top: 96px;
  }
  .contact__name {
    font-size: 19px;
    color: var(--red);
    line-height: 1.1;
  }
  .contact__role {
    font-size: 13px;
    color: var(--white);
    margin-top: 2px;
    margin-bottom: 8px;
  }
  .contact__list { list-style: none; }
  .contact__item {
    display: flex;
    align-items: center;
    gap: 8px;
    font-size: 12.5px;
    color: var(--white);
    line-height: 20px;
  }
  .contact__item svg { width: 11px; height: 11px; flex: none; }
  .divider {
    position: absolute;
    left: 24px;
    right: 24px;
    top: 222px;
    height: 1px;
    background: var(--rule);
  }
  .front-brand {
    position: absolute;
    right: 26px;
    top: 160px;
    display: flex;
    align-items: center;
    gap: 9px;
  }
  .front-brand__square {
    width: 18px;
    height: 18px;
    background: var(--red);
  }
  .front-brand__name {
    font-size: 26px;
    letter-spacing: 1.5px;
    text-transform: uppercase;
    color: var(--white);
    line-height: 1;
  }
  .address {
    position: absolute;
    right: 26px;
    top: 244px;
    text-align: right;
    font-size: 13px;
    line-height: 18px;
    font-style: normal;
    color: var(--white);
  }
</style>
</head>
<body>
<main class="sheet">
  <section class="card card--back" aria-label="Card back">
    <div class="brand-mark">
      <span class="brand-mark__square"></span>
      <span class="brand-mark__name">Quorvanex</span>
    </div>
    <p class="coupon-note">Sign up on our website for a coupon code</p>
  </section>

  <section class="card card--front" aria-label="Card front">
    <div class="contact">
      <p class="contact__name">Lorraine K. Vestal</p>
      <p class="contact__role">CEO</p>
      <ul class="contact__list">
        <li class="contact__item">
          <svg viewBox="0 0 12 12" aria-hidden="true"><path fill="#d8232a" d="M1 3c0-1 1-2 2-2h6c1 0 2 1 2 2v1H8V3H4v1H1zM2 5h8l1 6H1zM6 6.5a1.8 1.8 0 1 0 0 3.6 1.8 1.8 0 0 0 0-3.6z"/></svg>
          555.417.3820
        </li>
        <li class="contact__item">
          <svg viewBox="0 0 12 12" aria-hidden="true"><path fill="#d8232a" d="M0 2h12v1L6 7 0 3zM0 4.4l6 4 6-4V10H0z"/></svg>
          LVestal@Quorvanexco.com
        </li>
        <li class="contact__item">
          <svg viewBox="0 0 12 12" aria-hidden="true"><circle cx="6" cy="6" r="6" fill="#d8232a"/><path fill="none" stroke="#161617" stroke-width="1" d="M1 6h10M6 0.5c-2 2-2 9 0 11M6 0.5c2 2 2 9 0 11"/></svg>
          www.quorvanexco.com
        </li>
      </ul>
    </div>

    <div class="front-brand">
      <span class="front-brand__square"></span>
      <span class="front-brand__name">Quorvanex</span>
    </div>

    <div class="divider"></div>

    <address class="address">
      P.O. Box 47315<br>
      Alder Bay, Oregon 00000
    </address>
  </section>
</main>
</body>
</html>
```